Financial Services General Marketing Brochure

Need a brochure to help recipients understand what makes BWC unique and the services that we offer. Must match look/feel of website https://brightwellcustody.example Layouts should make it easy to read the content - content should not be crammed into a traditional size/layout. Please see attached creative brief for specifics.

Target Market(s)

Financial advisors and mature couples looking for trustee services.

Industry/Entity Type

Financial Service

Colors
34a7d8
ffc214

Requirements
Must have
• See Creative Brief

```html
<!DOCTYPE html>
<html lang="en">
<head>
<meta charset="utf-8">
<title>Brightwell Custody – Brochure Spread</title>
<link rel="stylesheet" href="https://fonts.googleapis.com/css2?family=Open+Sans:ital,wght@0,400;0,600;1,400&family=Noto+Serif:wght@400&family=Crimson+Pro:ital,wght@1,400&display=swap">
<style>
  :root {
    --paper: #ffffff;
    --trim: #b4b4b4;
    --panel-cream: #f7f3ee;
    --heading-blue: #4f6f90;
    --body-grey: #555555;
    --band-blue: #5d7c9c;
    --band-peach: #f5dfba;
    --band-orange: #f2b446;
    --brand-blue: #4f6f90;
    --brand-orange: #f39a2a;
    --white: #ffffff;
  }
  * { box-sizing: border-box; margin: 0; padding: 0; }
  html, body { width: 1200px; height: 1000px; overflow: hidden; background: var(--paper); }
  .spread { position: relative; width: 1200px; height: 1000px; }
  .trim-frame { position: absolute; left: 0; top: 199px; width: 1200px; height: 602px; border: 2px solid var(--trim); }
  .fold-line { position: absolute; left: 599px; top: 180px; width: 2px; height: 642px;
    background: repeating-linear-gradient(to bottom, var(--trim) 0 12px, transparent 12px 20px); }

  .photo { position: absolute; }
  .photo--advisor-meeting { left: 18px; top: 217px; width: 321px; height: 467px;
    background: linear-gradient(135deg, #e9edf1 0%, #b9c6d4 40%, #4d6a8e 75%, #c9a98d 100%); }
  .photo--family-autumn { left: 617px; top: 217px; width: 565px; height: 360px;
    background: linear-gradient(180deg, #f1ece0 0%, #b99a6a 45%, #8a5a2c 75%, #c98a3e 100%); }

  .info-panel { position: absolute; left: 339px; top: 217px; width: 244px; height: 467px;
    background: var(--panel-cream); padding: 13px 14px 0 14px; color: var(--body-grey);
    font-family: "Open Sans", sans-serif; font-size: 9.4px; line-height: 13px; }
  .info-panel h2 { font-family: "Noto Serif", serif; font-weight: 400; font-size: 18px;
    line-height: 22px; color: var(--heading-blue); margin-top: 10px; }
  .info-panel h2:first-child { margin-top: 0; }
  .info-panel .lead { font-style: italic; }
  .info-panel ul { list-style: none; margin-top: 8px; }
  .info-panel ul li::before { content: "•"; margin: 0 6px 0 2px; }
  .plain-list { list-style: none; margin-top: 0 !important; }
  .plain-list li::before { content: none !important; }

  .contact-band { position: absolute; left: 18px; top: 692px; width: 565px; height: 90px;
    background: var(--band-blue); display: flex; align-items: center; }
  .contact-band .brand-name { width: 300px; padding-left: 110px; font-family: "Open Sans", sans-serif;
    font-weight: 600; font-size: 22px; line-height: 24px; color: var(--white); }
  .contact-band .divider { width: 1px; height: 48px; background: rgba(255,255,255,.6); }
  .contact-band .contact-list { padding-left: 20px; list-style: none; font-family: "Open Sans", sans-serif;
    font-size: 12px; line-height: 20px; color: var(--white); }

  .brand-band { position: absolute; left: 617px; top: 585px; width: 565px; height: 106px;
    background: var(--band-peach); display: flex; align-items: center; justify-content: center; gap: 14px; }
  .brand-band .brand-dot { width: 26px; height: 26px; border-radius: 50%; background: var(--brand-orange); }
  .brand-band .brand-name { font-family: "Open Sans", sans-serif; font-weight: 600; font-size: 24px;
    color: var(--brand-blue); }

  .tagline-band { position: absolute; left: 617px; top: 691px; width: 565px; height: 91px;
    background: var(--band-orange); display: flex; align-items: center; justify-content: center; }
  .tagline-band p { font-family: "Crimson Pro", serif; font-style: italic; font-size: 29px;
    line-height: 31px; color: var(--white); text-align: center; }
</style>
</head>
<body>
<main class="spread">
  <div class="trim-frame"></div>
  <div class="fold-line"></div>

  <section class="back-panel">
    <div class="photo photo--advisor-meeting" role="img" aria-label="Photo of a smiling mature couple reviewing documents with an advisor"></div>

    <div class="info-panel">
      <h2>What We Offer</h2>
      <p class="lead">We specialize exclusively in the delivery of trustee and estate fiduciary services.</p>

      <h2>Who We Serve</h2>
      <ul class="plain-list">
        <li>Families</li>
        <li>Professional Advisors</li>
        <li>Foundations</li>
      </ul>

      <h2>How We Serve</h2>
      <p class="lead">Our expertise and experience is in family wealth. In this regard, we serve in the following ways:</p>
      <ul>
        <li>Trustee (Trusts)</li>
        <li>Executor and Personal Representative (Will)</li>
        <li>Agent for Financial Affairs (Power of Attorney)</li>
        <li>Trust Protector</li>
        <li>Special Independent Trustee</li>
        <li>Consultant</li>
        <li>Expert Witness</li>
      </ul>

      <h2>Trust Specialties</h2>
      <p class="lead">The general types of trusts on which we serve as trustee:</p>
      <ul>
        <li>Family Trusts</li>
        <li>Charitable Trusts</li>
        <li>Family Foundations</li>
        <li>Life Insurance Trusts</li>
        <li>Retirement Trusts</li>
        <li>Special Needs Trusts</li>
      </ul>
    </div>

    <footer class="contact-band">
      <div class="brand-name">Brightwell Custody</div>
      <div class="divider"></div>
      <ul class="contact-list">
        <li>555-014-2790</li>
        <li>info@brightwellcustody.example</li>
        <li>brightwellcustody.example</li>
      </ul>
    </footer>
  </section>

  <section class="cover-panel">
    <div class="photo photo--family-autumn" role="img" aria-label="Photo of a multi-generational family running hand in hand through autumn leaves"></div>
    <div class="brand-band">
      <span class="brand-dot"></span>
      <span class="brand-name">Brightwell Custody</span>
    </div>
    <div class="tagline-band">
      <p>Helping families protect and enrich<br>a multi-generational heritage</p>
    </div>
  </section>
</main>
</body>
</html>
```